Advertising company unique advertising platform

we need a logo design for a new company based in Australia Melbourne. We develop innovated advertising platform where consumer can use this platform to get regular discount, as business owner they can use this platform for free advertisement. Payment for this advertisement platform only payable every two weeks, when I generate revenue for their business

Industry/Entity Type

Advertising

Contact Information for Business Card

Dale Morven | Co-Founder |Managing Director
Suite 718 240 Wattlebrook Lane Melbourne Vic 3000

ABN 38 614 207 923
Tel: +61 0487 259 318 | Email: dale.morven@plivorantu.com

Font styles to use
Decorative
Script

Requirements
Must have
• Try few different design and some round corner business card
Should not have
• One round corner business card...try 4 different colour background not only black, make sure two side is designed. Be creative so imagine you are giving this to a client make sure has wow factor, if you can also try one design with engrave like all the logo, words look 3d feel
• The word Advertising Platform use attached file font

```html
<!DOCTYPE html>
<html lang="en">
<head>
<meta charset="utf-8">
<title>Brindle Loop business card</title>
<link rel="stylesheet" href="https://fonts.googleapis.com/css2?family=Roboto:wght@400;500;700&display=swap">
<style>
  :root {
    --page-bg: #3a3a3a;
    --card-dark: #232323;
    --card-light: #f6f6f4;
    --accent-red: #e8452c;
    --accent-teal: #1ed9b0;
    --accent-orange: #f07a28;
    --text-grey: #4a4a4a;
    --text-light: #d8d8d8;
    --ink: #111111;
    --wash-blue: rgba(169, 216, 234, 0.28);
    --wash-pink: rgba(244, 185, 174, 0.28);
  }
  * { box-sizing: border-box; margin: 0; padding: 0; }
  html, body { width: 1200px; height: 886px; overflow: hidden; }
  body {
    background: var(--page-bg);
    font-family: "Roboto", Arial, sans-serif;
    position: relative;
  }
  .card {
    position: absolute;
    left: 280px;
    width: 640px;
    height: 366px;
    border-radius: 26px;
    overflow: hidden;
  }
  .card--back { top: 50px; background: var(--card-dark); }
  .card--front { top: 470px; background: var(--card-light); }

  .brand {
    position: absolute;
    display: flex;
    align-items: center;
    gap: 14px;
    font-weight: 700;
    white-space: nowrap;
  }
  .brand__dot { border-radius: 50%; flex: none; }
  .card--back .brand {
    left: 50%; top: 130px; transform: translateX(-50%);
    font-size: 52px; color: var(--accent-orange);
  }
  .card--back .brand__dot { width: 62px; height: 62px; background: var(--accent-orange); }
  .website {
    position: absolute; left: 0; right: 0; bottom: 44px;
    text-align: center; color: var(--text-light);
    font-size: 15px; letter-spacing: 6px;
  }

  .wash {
    position: absolute; inset: 0;
    background:
      radial-gradient(ellipse 220px 160px at 36% 55%, var(--wash-blue), transparent 70%),
      radial-gradient(ellipse 240px 160px at 66% 60%, var(--wash-pink), transparent 70%);
  }
  .contact { position: absolute; left: 48px; top: 52px; }
  .contact__name {
    color: var(--accent-red); font-size: 22px; font-weight: 500;
    text-transform: uppercase; margin-bottom: 6px;
  }
  .contact__role {
    color: var(--accent-teal); font-size: 16px; font-weight: 500;
    text-transform: uppercase; line-height: 1.25; margin-bottom: 14px;
  }
  .contact__line { color: var(--text-grey); font-size: 15px; line-height: 1.4; }
  .contact__gap { margin-top: 12px; }
  .contact__item { display: flex; align-items: center; gap: 9px; }
  .contact__item svg { width: 14px; height: 14px; flex: none; }
  .card--front .brand {
    right: 40px; top: 158px;
    font-size: 34px; color: var(--ink);
  }
  .card--front .brand__dot { width: 46px; height: 46px; background: var(--ink); }
</style>
</head>
<body>
  <section class="card card--back" aria-label="Card back">
    <div class="brand"><span class="brand__dot"></span>Brindle Loop</div>
    <p class="website">www.plivorantu.com</p>
  </section>

  <section class="card card--front" aria-label="Card front">
    <div class="wash" role="img" aria-label="Faint pale blue and pink decorative pattern behind the card text"></div>
    <div class="contact">
      <p class="contact__name">Dale Morven</p>
      <p class="contact__role">Co-Founder<br>Managing Director</p>
      <p class="contact__line">Plivorantu</p>
      <p class="contact__line">ABN 38 614 207 923</p>
      <p class="contact__line contact__gap">Suite 718 240 Wattlebrook Lane</p>
      <p class="contact__line">Melbourne Vic 3000</p>
      <p class="contact__line contact__item contact__gap">
        <svg viewBox="0 0 16 16" aria-hidden="true"><path d="M3 1l3 0 1 4-2 1a9 9 0 0 0 5 5l1-2 4 1 0 3c0 1-1 2-2 2C7 15 1 9 1 3c0-1 1-2 2-2z" fill="var(--accent-red)"/></svg>
        +61 0487 259 318
      </p>
      <p class="contact__line contact__item">
        <svg viewBox="0 0 16 16" aria-hidden="true"><rect x="1" y="3" width="14" height="10" fill="var(--accent-red)"/><path d="M1 3l7 6 7-6" fill="none" stroke="#fff" stroke-width="1.5"/></svg>
        dale.morven@plivorantu.com
      </p>
    </div>
    <div class="brand"><span class="brand__dot"></span>Brindle Loop</div>
  </section>
</body>
</html>
```